New Wix logo and website layout

I need a new logo design and a new, modern website layout design. I am a professional therapist providing remedial massage. I am Canadian but live in Australia & would like the logo to have a somewhat 'Canadian feel' to it (something subtle i.e. no flags) I currently have a maple tree leaf as my logo. my current website is tidewaterbodywork.com.au. I need the website to work on mobile phones & traditional web browsers.

Target Market(s)

customers looking for remedial massage and manual lymphatic drainage

Industry/Entity Type

professional massage

Coding

Coded - Design and coding required

Font styles to use
Sans Serif

Colors
EB3D1F
EC4F4E
F09395
F8D3D4
FCEDEE

Requirements
Nice to have
• something subtle that indicates that I am canadian
Should not have
• no flags. nothing too bold

```html
<!DOCTYPE html>
<html lang="en">
<head>
<meta charset="utf-8">
<title>Tidewater Bodywork – Remedial Massage</title>
<link href="https://fonts.googleapis.com/css2?family=Josefin+Sans:wght@400;600;700&family=Lato:wght@400;700&display=swap" rel="stylesheet">
<style>
:root{
  --red:#eb3d1f;
  --coral:#ec4f4e;
  --pink:#f09395;
  --blush:#f8d3d4;
  --mist:#fcedee;
  --ink:#111;
  --text:#333;
  --muted:#9a9a9a;
  --grey-bg:#f1f1f1;
  --white:#fff;
}
*{box-sizing:border-box;margin:0;padding:0}
html,body{width:1200px;height:3717px;overflow:hidden;background:var(--white)}
body{position:relative;font-family:'Lato',sans-serif;color:var(--text)}
.abs{position:absolute}
.display{font-family:'Josefin Sans',sans-serif;font-weight:700;color:var(--ink)}
.btn{position:absolute;display:flex;align-items:center;justify-content:center;border-radius:40px;background:var(--red);color:var(--white);font-family:'Josefin Sans',sans-serif;font-weight:700;font-size:15px}

/* hero */
.hero-bg{left:0;top:0;width:1200px;height:860px;background:radial-gradient(circle at 62% 22%,#e07a28 0,#b3501c 22%,#5a2a14 45%,#2f4a4c 70%,#1f2e30 100%)}
.curves{left:0;top:0}
.top-info{top:16px;font-size:15px;color:var(--white);display:flex;align-items:center;gap:8px}
.badge{left:111px;top:0;width:143px;height:173px;background:var(--white);border-radius:0 0 72px 72px;display:flex;flex-direction:column;align-items:center;padding-top:18px;gap:8px}
.badge .dot{width:76px;height:76px;border-radius:50%;background:var(--red)}
.badge .name{font-family:'Josefin Sans',sans-serif;font-weight:700;font-size:13px;color:var(--ink);text-align:center;line-height:1.15}
.nav{left:254px;top:60px;width:758px;height:67px;background:var(--white);border-radius:0 40px 40px 0;display:flex;align-items:center;padding-left:38px;gap:54px;font-size:15px;color:#222}
.nav .btn{position:static;width:112px;height:46px;margin-left:auto;margin-right:12px}
.welcome{left:116px;top:260px;font-family:'Josefin Sans',sans-serif;font-size:29px;color:var(--red)}
.hero-title{left:112px;top:296px;font-size:66px;line-height:68px;color:var(--white)}
.hero-text{left:116px;top:432px;font-size:16px;line-height:26px;color:var(--white);width:420px}

/* about */
.about-photo{left:99px;top:888px;width:464px;height:464px;border-radius:50%;background:radial-gradient(circle at 45% 40%,#f7a07a 0,var(--coral) 40%,var(--red) 75%,#c92b10 100%)}
.about-title{left:594px;top:940px;font-size:41px}
.about-text{left:591px;top:999px;width:490px;font-size:15px;line-height:26px;color:#333}
.about-text p+p{margin-top:25px}

/* services */
.services{left:0;top:1445px;width:1200px;height:617px;background:var(--grey-bg)}
.sec-title{width:1200px;left:0;text-align:center;font-size:35px}
.card{top:1581px;width:293px;height:404px;background:var(--white);border-radius:4px;text-align:center}
.card .pic{height:175px;border-radius:0 0 146px 146px/0 0 120px 120px;background:linear-gradient(160deg,#5b4236,#a47a62 55,#d9b7a0)}
.card h3{font-family:'Josefin Sans',sans-serif;font-weight:700;font-size:27px;color:var(--ink);margin:22px 0 10px}
.card p{font-size:15px;line-height:26px;padding:0 30px}
.card .arrow{margin-top:22px}
.card-bar{top:1985px;width:260px;height:9px;background:#ddd}
.circ{width:38px;height:38px;border-radius:50%;display:flex;align-items:center;justify-content:center}

/* remedial band */
.band{left:0;top:2062px;width:1200px;height:380px;background:linear-gradient(110deg,#e0391b,#eb3d1f 45%,#ef5a3d)}
.band h2{font-family:'Josefin Sans',sans-serif;font-weight:700;font-size:37px;color:var(--white);text-align:center;margin-top:55px}
.band p{width:880px;margin:20px auto 0;text-align:center;font-size:15px;line-height:26px;color:var(--white)}
.band .btn{left:522px;top:246px;width:150px;height:53px;background:var(--white);color:var(--red);font-size:13px}

/* fees */
.fee{background:var(--white);text-align:center;box-shadow:0 10px 40px rgba(0,0,0,.08)}
.fee .price{font-family:'Josefin Sans',sans-serif;font-weight:700;font-size:33px;color:var(--red)}
.fee h3{font-family:'Josefin Sans',sans-serif;font-weight:700;font-size:26px;color:var(--ink);margin-top:6px}
.fee .mins{font-family:'Josefin Sans',sans-serif;font-size:14px;color:var(--muted);margin-top:6px}
.fee p{font-size:15px;line-height:30px;color:var(--muted);padding:0 26px;margin-top:8px}
.fee .btn{position:relative;margin:22px auto 0;width:156px;height:49px}

/* footer */
.f-logo{left:509px;top:3224px;width:164px;height:164px;border-radius:50%;background:var(--red)}
.f-name{left:0;width:1182px;top:3405px;text-align:center;font-family:'Josefin Sans',sans-serif;font-weight:700;font-size:29px;color:var(--white)}
.f-nav{left:315px;top:3490px;display:flex;gap:54px;font-size:15px;color:var(--white)}
.copy{left:0;width:1188px;top:3562px;text-align:center;font-size:13px;color:var(--white)}
.copy a{color:var(--red)}
.social{top:3614px;width:44px;height:44px;border-radius:50%}
</style>
</head>
<body>

<!-- Hero -->
<div class="abs hero-bg" role="img" aria-label="Close-up photograph of autumn maple leaves on a blurred background"></div>
<svg class="abs curves" width="1200" height="900" viewBox="0 0 1200 900">
  <path d="M0 705 C300 800 700 850 1200 705 L1200 900 L0 900Z" fill="#eb3d1f"/>
  <path d="M0 705 C300 790 650 815 1200 832 L1200 900 L0 900Z" fill="#fff"/>
</svg>

<div class="abs top-info" style="left:300px">
  <svg width="12" height="15" viewBox="0 0 12 15"><path d="M6 0a6 6 0 0 0-6 6c0 4.5 6 9 6 9s6-4.5 6-9a6 6 0 0 0-6-6zm0 8.3A2.3 2.3 0 1 1 6 3.7a2.3 2.3 0 0 1 0 4.6z" fill="#eb3d1f"/></svg>
  12 Harbour Lane Seaford VIC 3198
</div>
<div class="abs top-info" style="left:726px">
  <svg width="15" height="11" viewBox="0 0 15 11"><rect width="15" height="11" rx="1.5" fill="#eb3d1f"/><path d="M1 1l6.5 5L14 1" stroke="#fff" stroke-width="1.3" fill="none"/></svg>
  hello@tidewaterbodywork.com.au
</div>

<div class="abs badge">
  <div class="dot"></div>
  <div class="name">TIDEWATER<br>BODYWORK</div>
</div>

<nav class="abs nav">
  <span>Home</span><span>Remedial Massage</span><span>About Me</span><span>Fees</span><span>Contact</span>
  <span class="btn">Login</span>
</nav>

<div class="abs welcome">Welcome To</div>
<h1 class="abs display hero-title">TIDEWATER<br>BODYWORK</h1>
<p class="abs hero-text">I completed my training in Toronto, Canada in 1999 where I obtained a Diploma of Remedial Massage ....</p>
<span class="btn" style="left:112px;top:499px;width:179px;height:63px">Get Started</span>

<!-- About -->
<div class="abs about-photo" role="img" aria-label="Photograph of a person with arms raised, framed inside a leaf shape with red tones"></div>
<h2 class="abs display about-title">About Tidewater Bodywork</h2>
<div class="abs about-text">
  <p>I completed my training in Toronto, Canada in 1999 where I obtained a Diploma of Remedial Massage through the Northfield College of Massage &amp; Hydrotherapy.</p>
  <p>Over the years, I have practiced in several different settings including medical centre, chiropractic clinic, spa and currently am a sole trader in my own practice. I have been helping my clients achieve better health through my treatments for several years. I take special interest in women's health.</p>
</div>
<span class="btn" style="left:588px;top:1255px;width:150px;height:55px;font-size:13px">Learn More</span>

<!-- Services -->
<div class="abs services"></div>
<h2 class="abs display sec-title" style="top:1500px">Our Services</h2>

<div class="abs card-bar" style="left:142px"></div>
<div class="abs card-bar" style="left:467px;background:var(--red)"></div>
<div class="abs card-bar" style="left:792px"></div>

<div class="abs card" style="left:125px">
  <div class="pic" role="img" aria-label="Photograph of a therapist massaging a client's shoulders"></div>
  <h3>Remedial</h3>
  <p>Lorem ipsum dolor sit amet, consectetur adipiscing elit, sed do eiusmod tempor incididunt ut labore et dolore magna aliqua.</p>
  <svg class="arrow" width="22" height="18" viewBox="0 0 22 18"><path d="M1 9h19M12 1l8 8-8 8" stroke="#999" stroke-width="2" fill="none"/></svg>
</div>
<div class="abs card" style="left:450px">
  <div class="pic" style="background:linear-gradient(160deg,#3a2416,#8a4e2c 55%,#c98656)" role="img" aria-label="Photograph of a deep tissue back massage"></div>
  <h3>Deep Tissue</h3>
  <p>Lorem ipsum dolor sit amet, consectetur adipiscing elit, sed do eiusmod tempor incididunt ut labore et dolore magna aliqua.</p>
  <svg class="arrow" width="22" height="18" viewBox="0 0 22 18"><path d="M1 9h19M12 1l8 8-8 8" stroke="#eb3d1f" stroke-width="2" fill="none"/></svg>
</div>
<div class="abs card" style="left:775px">
  <div class="pic" style="background:linear-gradient(160deg,#e9e4df,#cfc6bd 55%,#a9a29b)" role="img" aria-label="Photograph of therapeutic taping on a client's shoulder"></div>
  <h3>Therapeutic</h3>
  <p>Lorem ipsum dolor sit amet, consectetur adipiscing elit, sed do eiusmod tempor incididunt ut labore et dolore magna aliqua.</p>
  <svg class="arrow" width="22" height="18" viewBox="0 0 22 18"><path d="M1 9h19M12 1l8 8-8 8" stroke="#999" stroke-width="2" fill="none"/></svg>
</div>

<div class="abs circ" style="left:93px;top:1784px;background:#ddd"><svg width="8" height="12"><path d="M6 1L2 6l4 5" stroke="#eb3d1f" stroke-width="1.6" fill="none"/></svg></div>
<div class="abs circ" style="left:1058px;top:1784px;background:var(--red)"><svg width="8" height="12"><path d="M2 1l4 5-4 5" stroke="#fff" stroke-width="1.6" fill="none"/></svg></div>

<!-- Remedial band -->
<section class="abs band" role="img" aria-label="Photograph of hands giving a massage under a red overlay">
  <h2>Remedial Massage</h2>
  <p>Remedial massage is used to help relieve tension and stress in the soft tissues of the body including muscles, tendons, ligaments and connective tissue. It helps to alleviate soft tissue discomfort associated with everyday and occupational stress, over-use injuries e.g. tendinitis, and many chronic pain conditions.&nbsp; An increase in circulation and increased joint flexibility are additional benefits.</p>
  <span class="btn">Learn More</span>
</section>

<!-- Fees -->
<h2 class="abs display sec-title" style="top:2537px">Fee Schedule</h2>

<div class="abs fee" style="left:162px;top:2596px;width:275px;height:414px;padding-top:20px">
  <div class="price">$110</div>
  <h3>Remedial Massage</h3>
  <div class="mins">60 min</div>
  <p>Lorem ipsum dolor sit amet, consectetur adipiscing elit, sed do eiusmod tempor incididunt ut labore et dolore magna aliqua. Quis ipsum suspendisse ultrices gravida. Risus commodo viverra maecenas.</p>
  <span class="btn">Choose Plan</span>
</div>
<div class="abs fee" style="left:753px;top:2596px;width:278px;height:414px;padding-top:16px">
  <div class="price">$90</div>
  <h3>Remedial Massage</h3>
  <div class="mins">45 &nbsp;min</div>
  <p>Lorem ipsum dolor sit amet, consectetur adipiscing elit, sed do eiusmod tempor incididunt ut labore et dolore magna aliqua. Quis ipsum suspendisse ultrices gravida. Risus commodo viverra maecenas .</p>
  <span class="btn">Choose Plan</span>
</div>
<div class="abs fee" style="left:437px;top:2572px;width:316px;height:464px;padding-top:44px;box-shadow:0 10px 50px rgba(0,0,0,.12)">
  <div class="price">$70</div>
  <h3>Remedial Massage</h3>
  <div class="mins">30 min</div>
  <p>Lorem ipsum dolor sit amet, consectetur adipiscing elit, sed do eiusmod tempor incididunt ut labore et dolore magna aliqua. Quis ipsum suspendisse ultrices gravida. Risus commodo viverra maecenas accumsan lacus vel facilisis.</p>
  <span class="btn" style="width:178px;height:56px;font-size:16px">Choose Plan</span>
</div>

<div class="abs circ" style="left:99px;top:2783px;background:var(--blush)"><svg width="8" height="12"><path d="M6 1L2 6l4 5" stroke="#eb3d1f" stroke-width="1.6" fill="none"/></svg></div>
<div class="abs circ" style="left:1064px;top:2783px;background:var(--red)"><svg width="8" height="12"><path d="M2 1l4 5-4 5" stroke="#fff" stroke-width="1.6" fill="none"/></svg></div>

<!-- Footer -->
<svg class="abs" style="left:0;top:3100px" width="1200" height="617" viewBox="0 0 1200 617">
  <path d="M0 120 C350 20 800 10 1200 35 L1200 617 L0 617Z" fill="#eb3d1f"/>
  <path d="M0 145 C350 50 800 45 1200 100 L1200 617 L0 617Z" fill="#000"/>
</svg>
<div class="abs f-logo"></div>
<div class="abs f-name">TIDEWATER BODYWORK</div>
<div class="abs f-nav"><span>Home</span><span>Remedial Massage</span><span>About Me</span><span>Fees</span><span>Contact</span></div>
<div class="abs copy">Copyright© 2022 &nbsp;<a href="#">Tidewater Bodywork</a>&nbsp; | &nbsp;All Rights Reserved</div>
<span class="abs social" style="left:491px;background:var(--red)"></span>
<span class="abs social" style="left:543px;background:var(--white)"></span>
<span class="abs social" style="left:594px;background:var(--white)"></span>
<span class="abs social" style="left:646px;background:var(--white)"></span>

</body>
</html>
```